Company Business Card (Company Promotions)

We want a Business Card that is both Elegant & High Class. We want the card stock thick and unique. We want it to build our Brand Name. We service Automobile dealerships & owners who drive luxury & exotic automobiles that cost an average of $75K. We provide towing services for Luxury & Exotic vehicles. Our colors are Black & Construction Yellow (Gold).
We are manufacture certified for Valdora Kent, RQT, PUKA, ELVO, Tavrine, HJ, Colvesi, Pendrel, Casteduvro, Ombra & Sorvanel. We have authorization to use their logo's.
Enclosed is our old business card. We only used the unusual & Unique brands on the cards but are open to the use of all of them. We also use the Federal Competence Badge that identifies our abilities.

Also enclosed is the name font that we use.

Target Market(s)

Business, Executive, Hi end people that drive finer luxury &/or exotic automobiles.

Industry/Entity Type

Business

Contact Information for Business Card

We market our name. Haul Crestmark. Business address is: 4812 Willowmere Lane, NE Ste: 210, Atlanta, GA 30399 Phone: 404-555-0148. Web address is crestmarkhaul-example.com
Manufacture Certified / Nationally Certified

Font styles to use
Other font styles liked:
• AR DESTINE (in Italic's)

Colors
ffc214

Requirements
Must have
• Must have the at least 5 of the manufacture logo's and the Guild Council Emblem (see on other business card)
Nice to have
• Place the manfacture logo's on the back.
Should not have
• No other colors than Black, Yellow & White

```html
<!DOCTYPE html>
<html lang="en">
<head>
<meta charset="utf-8">
<title>Haul Crestmark – Business Card</title>
<link rel="stylesheet" href="https://fonts.googleapis.com/css2?family=Russo+One&family=Tinos:wght@700&display=swap">
<style>
  :root {
    --black: #000000;
    --ink: #0b0b0b;
    --yellow: #ffc214;
    --white: #ffffff;
    --backdrop: #e9e6df;
    --muted: #3a3a3a;
  }
  * { margin: 0; padding: 0; box-sizing: border-box; }
  html, body { width: 1200px; height: 858px; overflow: hidden; }
  body {
    background: var(--backdrop);
    position: relative;
    font-family: "Tinos", "Times New Roman", serif;
  }
  .card {
    position: absolute;
    width: 540px;
    height: 309px;
    background: var(--ink);
    overflow: hidden;
    box-shadow: 0 6px 18px rgba(0,0,0,0.25);
  }
  .card--front { left: 40px; top: 275px; }
  .card--back  { left: 620px; top: 275px; }

  /* front */
  .front-curve { position: absolute; inset: 0; }
  .badge {
    position: absolute;
    right: 122px; top: 14px;
    width: 78px; height: 88px;
  }
  .brand-name {
    position: absolute;
    left: 34px; top: 104px;
    font-family: "Russo One", "Arial Black", sans-serif;
    color: var(--yellow);
    font-size: 32px;
    letter-spacing: 1px;
    line-height: 1;
    white-space: nowrap;
  }
  .brand-rule {
    position: absolute;
    left: 34px; top: 146px;
    width: 300px; height: 2px;
    background: var(--yellow);
  }
  .tagline {
    position: absolute;
    left: 34px; top: 154px;
    color: var(--yellow);
    font-size: 14px;
    font-weight: 700;
    white-space: nowrap;
  }
  .contact {
    position: absolute;
    left: 110px; top: 190px;
    list-style: none;
    color: var(--white);
    font-size: 15px;
    font-weight: 700;
    line-height: 1.3;
  }
  .contact li { display: flex; align-items: flex-start; gap: 8px; white-space: nowrap; }
  .contact svg { flex: none; margin-top: 3px; }

  /* back */
  .marque-strip {
    position: absolute;
    left: 0; top: 0; bottom: 0;
    width: 128px;
    background: var(--white);
    display: flex;
    flex-direction: column;
    justify-content: space-evenly;
    padding: 10px 12px;
  }
  .marque {
    display: flex; align-items: center; gap: 6px;
    font-size: 12px; font-weight: 700;
    color: var(--black);
    white-space: nowrap;
  }
  .marque::before {
    content: "";
    width: 12px; height: 12px;
    border: 1.5px solid var(--black);
    border-radius: 50%;
    flex: none;
  }
  .back-rule {
    position: absolute;
    left: 140px; top: 0; bottom: 0;
    width: 4px;
    background: var(--yellow);
  }
  .badge-faint {
    position: absolute;
    right: 26px; top: 14px;
    width: 116px; height: 128px;
    opacity: 0.22;
  }
  .back-name {
    position: absolute;
    left: 190px; top: 150px;
    font-family: "Russo One", "Arial Black", sans-serif;
    color: var(--yellow);
    line-height: 1;
    white-space: nowrap;
  }
  .back-name .line-1 { display: block; font-size: 34px; }
  .back-name .line-2 { display: block; font-size: 50px; margin-top: 6px; }
</style>
</head>
<body>

<section class="card card--front" aria-label="Business card front">
  <svg class="front-curve" viewBox="0 0 540 309" aria-hidden="true">
    <path d="M440 0 Q470 190 350 309 L540 309 L540 0 Z" fill="var(--white)"/>
    <path d="M452 0 Q482 195 366 309 L540 309 L540 0 Z" fill="var(--yellow)"/>
  </svg>

  <svg class="badge" viewBox="0 0 86 96" role="img" aria-label="Federal Competence Badge with Guild Council Emblem">
    <path d="M4 8 Q43 -4 82 8 L82 50 Q82 80 43 94 Q4 80 4 50 Z" fill="var(--white)" stroke="var(--yellow)" stroke-width="3"/>
    <path d="M14 18 Q43 10 72 18 L72 50 Q72 72 43 84 Q14 72 14 50 Z" fill="var(--muted)"/>
  </svg>

  <div class="brand-name">Haul Crestmark</div>
  <div class="brand-rule"></div>
  <div class="tagline">Manufacture Certified / Nationally Certified</div>

  <ul class="contact">
    <li>
      <svg width="12" height="12" viewBox="0 0 12 12" aria-hidden="true"><rect width="12" height="12" rx="2" fill="var(--white)"/><path d="M3 3 L5 3 L5.5 5 L4.6 5.8 Q5.5 7.4 6.2 7.4 L7 6.5 L9 7 L9 9 Q4 9.5 3 3 Z" fill="var(--black)"/></svg>
      404-555-0148
    </li>
    <li>
      <svg width="12" height="12" viewBox="0 0 12 12" aria-hidden="true"><rect width="12" height="12" rx="2" fill="var(--white)"/><rect x="3" y="3" width="6" height="6" fill="none" stroke="var(--black)" stroke-width="1.2"/></svg>
      404-555-0172
    </li>
    <li>
      <svg width="12" height="12" viewBox="0 0 12 12" aria-hidden="true"><rect width="12" height="12" rx="2" fill="var(--white)"/><circle cx="6" cy="6" r="3" fill="none" stroke="var(--black)" stroke-width="1.2"/></svg>
      crestmarkhaul-example.com
    </li>
    <li>
      <svg width="12" height="12" viewBox="0 0 12 12" aria-hidden="true"><rect width="12" height="12" rx="2" fill="var(--white)"/><path d="M6 2.5 A2.5 2.5 0 0 1 8.5 5 Q8.5 7 6 9.5 Q3.5 7 3.5 5 A2.5 2.5 0 0 1 6 2.5 Z" fill="var(--black)"/></svg>
      <span>4812 Willowmere Lane, NE Ste:<br>210, Atlanta, GA 30399</span>
    </li>
  </ul>
</section>

<section class="card card--back" aria-label="Business card back">
  <div class="marque-strip">
    <span class="marque">Harlven</span>
    <span class="marque">Mevrin</span>
    <span class="marque">Tavrine</span>
    <span class="marque">Valdora Kent</span>
    <span class="marque">ELVO</span>
    <span class="marque">Pendrel</span>
    <span class="marque">Jorvane</span>
  </div>
  <div class="back-rule"></div>

  <svg class="badge-faint" viewBox="0 0 86 96" role="img" aria-label="Faint Federal Competence Badge">
    <path d="M4 8 Q43 -4 82 8 L82 50 Q82 80 43 94 Q4 80 4 50 Z" fill="var(--white)"/>
  </svg>

  <div class="back-name">
    <span class="line-1">Haul</span>
    <span class="line-2">Crestmark</span>
  </div>
</section>

</body>
</html>
```